professional business card design for technology company

We are a small technology consulting firm, specialising in consulting based around Cloud and Managed services. Our colour scheme is yellow, blue and white, as you can see in the logos. Although we are based in melbourne australia, due to the nature of our work, our clients can be located anywhere. We are looking for a clean, professional, positive look - similar to our company logo

Target Market(s)

small business

Industry/Entity Type

Business

Contact Information for Business Card

eye catching, designed to incorporate some level of raised printing. Must contain website address, phone number, name and job title

Requirements
Must have
• Logo (attached) - use of the same colour scheme

```html
<!DOCTYPE html>
<html lang="en">
<head>
<meta charset="utf-8">
<title>Nimbara Business Card</title>
<link rel="stylesheet" href="https://fonts.googleapis.com/css2?family=Lato:wght@400;700;900&family=Arimo:wght@400&display=swap">
<style>
  :root {
    --backdrop: #2a2d2f;
    --card-light: #eef1f0;
    --card-dark: #4a5756;
    --sky-blue: #4fc3ef;
    --ink: #3d4444;
    --ink-soft: #444a4a;
    --white: #ffffff;
  }
  * { margin: 0; padding: 0; box-sizing: border-box; }
  html, body {
    width: 1200px;
    height: 864px;
    overflow: hidden;
    background: var(--backdrop);
  }
  .canvas {
    position: relative;
    width: 1200px;
    height: 864px;
  }
  .card {
    position: absolute;
    overflow: hidden;
  }
  .card--front {
    left: 332px; top: 85px; width: 540px; height: 317px;
    background: var(--card-light);
  }
  .card--back {
    left: 325px; top: 455px; width: 551px; height: 306px;
    background: var(--card-dark);
  }
  .holder {
    position: absolute;
    left: 48px; top: 50px;
  }
  .holder__name {
    font-family: "Lato", sans-serif;
    font-weight: 700;
    font-size: 23px;
    line-height: 28px;
    color: var(--sky-blue);
  }
  .holder__role {
    font-family: "Lato", sans-serif;
    font-weight: 400;
    font-size: 17px;
    line-height: 22px;
    color: var(--ink-soft);
  }
  .contact {
    position: absolute;
    left: 48px; top: 168px;
    list-style: none;
  }
  .contact__label {
    font-family: "Arimo", sans-serif;
    font-size: 14px;
    line-height: 18px;
    color: var(--sky-blue);
  }
  .contact__value {
    font-family: "Arimo", sans-serif;
    font-size: 14.5px;
    line-height: 19.5px;
    color: var(--ink-soft);
  }
  .brand {
    position: absolute;
    display: flex;
    align-items: center;
    font-family: "Lato", sans-serif;
    font-weight: 900;
    letter-spacing: -0.5px;
  }
  .brand__dot {
    border-radius: 50%;
    flex: none;
  }
  .brand--front {
    right: 30px; top: 122px;
    font-size: 42px;
    color: var(--ink);
  }
  .brand--front .brand__dot {
    width: 34px; height: 34px;
    margin-right: 14px;
    background: var(--sky-blue);
  }
  .brand--back {
    left: 176px; top: 114px;
    font-size: 62px;
    color: var(--white);
  }
  .brand--back .brand__dot {
    width: 46px; height: 46px;
    margin-right: 18px;
    background: var(--white);
  }
</style>
</head>
<body>
<main class="canvas">
  <section class="card card--front" aria-label="Business card front">
    <div class="holder">
      <h1 class="holder__name">Alex Moreton</h1>
      <p class="holder__role">Managing Director</p>
    </div>
    <ul class="contact">
      <li class="contact__label">telephone</li>
      <li class="contact__value">055-987 654 321</li>
      <li class="contact__label">email</li>
      <li class="contact__value">info@sitename.com</li>
      <li class="contact__label">address</li>
      <li class="contact__value">5678, street name here, country</li>
    </ul>
    <div class="brand brand--front">
      <span class="brand__dot"></span>
      <span class="brand__name">Nimbara</span>
    </div>
  </section>

  <section class="card card--back" aria-label="Business card back">
    <div class="brand brand--back">
      <span class="brand__dot"></span>
      <span class="brand__name">Nimbara</span>
    </div>
  </section>
</main>
</body>
</html>
```